Bref créative
Letterhead/Envelope/Business Card/Other Stationary
The Montrevo Group
Professional
Kelvin Ostrander
President
4317 West Pellham Avenue
Niles, IL 60823
Kelvin.Ostrander@montrevogroup.example
Please do not use any initials like "TMG". Use the attached logo. Also, besides the business card, I would like to see designs for Letterhead, Envelope, Fax Cover and Email Signature.
I am open to it. However, should be modern, corporate and professional.
Franchises
I have attached a white logo on transparent background
I am also attaching dark blue font text for putting on a white background

```html
<!DOCTYPE html>
<html lang="en">
<head>
<meta charset="utf-8">
<title>The Montrevo Group — Stationery</title>
<link rel="stylesheet" href="https://fonts.googleapis.com/css2?family=Cormorant+SC:wght@500&family=Open+Sans:wght@400;600&display=swap">
<style>
  :root {
    --brand-blue: #3f5b93;
    --brand-blue-light: #6f87b8;
    --paper: #ffffff;
    --backdrop: #e6e7ea;
    --ink-soft: #8a93a6;
    --watermark: #eef0f5;
  }
  * { box-sizing: border-box; margin: 0; padding: 0; }
  html, body { width: 1200px; height: 466px; overflow: hidden; }
  body { background: var(--backdrop); font-family: "Open Sans", sans-serif; position: relative; }

  .sheet { position: absolute; background: var(--paper); box-shadow: 0 2px 6px rgba(0,0,0,.18); overflow: hidden; }
  .wave { position: absolute; left: 0; bottom: 0; width: 100%; }
  .wordmark { font-family: "Cormorant SC", serif; font-weight: 500; color: var(--brand-blue); display: flex; align-items: center; gap: 5px; white-space: nowrap; }
  .wordmark .mark-box { border: 1px solid var(--brand-blue); display: inline-block; }
  .caption { position: absolute; font-size: 5px; letter-spacing: .6px; text-transform: uppercase; color: #6b7080; text-align: center; }

  /* business cards */
  .card-front { left: 12px; top: 245px; width: 90px; height: 58px; }
  .card-front .wordmark { position: absolute; left: 7px; top: 8px; font-size: 6px; }
  .card-front .wordmark .mark-box { width: 7px; height: 7px; }
  .card-front .person { position: absolute; left: 7px; top: 22px; font-size: 3.5px; color: var(--ink-soft); line-height: 1.4; }
  .card-back { left: 12px; top: 330px; width: 90px; height: 58px; background: var(--brand-blue); }
  .card-back .wordmark { position: absolute; inset: 0; justify-content: center; color: var(--paper); font-size: 7px; }

  /* letterheads */
  .letterhead { top: 43px; width: 360px; height: 384px; }
  .letterhead-one { left: 228px; }
  .letterhead-two { left: 617px; }
  .letterhead .wordmark { position: absolute; left: 28px; top: 28px; font-size: 10px; }
  .letterhead .wordmark .mark-box { width: 12px; height: 12px; }
  .contact-block { position: absolute; right: 30px; top: 28px; font-size: 4.5px; color: var(--ink-soft); line-height: 1.9; }
  .contact-block li { list-style: none; display: flex; align-items: center; gap: 4px; }
  .contact-block .dot { width: 4px; height: 4px; border-radius: 50%; background: var(--brand-blue-light); }
  .watermark { position: absolute; left: 110px; top: 110px; width: 140px; height: 140px; border-radius: 50%; background: var(--watermark); }
  .footer-line { position: absolute; left: 0; right: 0; bottom: 34px; text-align: center; font-size: 4.5px; color: var(--paper); letter-spacing: .3px; z-index: 2; }

  /* envelopes */
  .envelope { left: 1008px; width: 185px; }
  .env-front { top: 43px; height: 84px; }
  .env-front .wordmark { position: absolute; left: 0; right: 0; top: 18px; justify-content: center; font-size: 6px; }
  .env-front .wordmark .mark-box { width: 8px; height: 8px; }
  .env-back { top: 132px; height: 84px; background: var(--paper); }
  .env-plain { top: 224px; height: 80px; }
  .env-long { top: 312px; height: 106px; }
  .env-long .wordmark { position: absolute; left: 12px; top: 30px; font-size: 8px; }
  .env-long .wordmark .mark-box { width: 10px; height: 10px; }
  .env-long .tagline { position: absolute; left: 29px; top: 44px; font-size: 4px; color: var(--ink-soft); }
</style>
</head>
<body>

  <!-- business card front -->
  <div class="sheet card-front">
    <div class="wordmark"><span class="mark-box"></span>The Montrevo Group</div>
    <div class="person">Kelvin Ostrander<br>President</div>
    <svg class="wave" viewBox="0 0 360 70" preserveAspectRatio="none" height="14">
      <path d="M0 32 C120 2 240 52 360 16 L360 70 L0 70Z" fill="var(--brand-blue)"/>
    </svg>
  </div>
  <p class="caption" style="left:12px; top:308px; width:90px;">Business Card Front</p>

  <!-- business card back -->
  <div class="sheet card-back">
    <div class="wordmark">The Montrevo Group</div>
  </div>
  <p class="caption" style="left:12px; top:393px; width:90px;">Business Card Back</p>
  <p class="caption" style="left:12px; top:232px; width:90px;">Stationery Concepts</p>

  <!-- letterhead option 1 -->
  <div class="sheet letterhead letterhead-one">
    <div class="wordmark"><span class="mark-box"></span>The Montrevo Group</div>
    <ul class="contact-block">
      <li><span class="dot"></span>4317 West Pellham Avenue</li>
      <li><span class="dot"></span>Niles, IL 60823</li>
      <li><span class="dot"></span>Tel: (847) 555-0142</li>
      <li><span class="dot"></span>Kelvin.Ostrander@montrevogroup.example</li>
    </ul>
    <svg class="wave" viewBox="0 0 360 70" preserveAspectRatio="none" height="64">
      <path d="M0 34 C110 4 230 56 360 18 L360 70 L0 70Z" fill="var(--brand-blue)"/>
      <path d="M0 26 C110 -2 230 50 360 10" fill="none" stroke="var(--brand-blue-light)" stroke-width="1.4"/>
      <path d="M0 46 C120 18 240 62 360 30" fill="none" stroke="var(--paper)" stroke-width=".8" opacity=".7"/>
    </svg>
  </div>
  <p class="caption" style="left:228px; top:432px; width:360px;">Letter Head Option 1</p>

  <!-- letterhead option 2 -->
  <div class="sheet letterhead letterhead-two">
    <div class="wordmark"><span class="mark-box"></span>The Montrevo Group</div>
    <div class="watermark"></div>
    <p class="footer-line">4317 West Pellham Avenue, Niles, IL 60823 &nbsp;|&nbsp; Tel: (847) 555-0142 &nbsp;|&nbsp; Kelvin.Ostrander@montrevogroup.example</p>
    <svg class="wave" viewBox="0 0 360 70" preserveAspectRatio="none" height="64">
      <path d="M0 34 C110 4 230 56 360 18 L360 70 L0 70Z" fill="var(--brand-blue)"/>
      <path d="M0 26 C110 -2 230 50 360 10" fill="none" stroke="var(--brand-blue-light)" stroke-width="1.4"/>
      <path d="M0 46 C120 18 240 62 360 30" fill="none" stroke="var(--paper)" stroke-width=".8" opacity=".7"/>
    </svg>
  </div>
  <p class="caption" style="left:617px; top:432px; width:360px;">Letter Head Option 2</p>

  <!-- envelopes -->
  <div class="sheet envelope env-front">
    <div class="wordmark"><span class="mark-box"></span>The Montrevo Group</div>
    <svg class="wave" viewBox="0 0 360 70" preserveAspectRatio="none" height="34">
      <path d="M0 30 C110 4 230 52 360 16 L360 70 L0 70Z" fill="var(--brand-blue)"/>
      <path d="M0 22 C110 -4 230 46 360 8" fill="none" stroke="var(--brand-blue-light)" stroke-width="1.4"/>
    </svg>
  </div>

  <div class="sheet envelope env-back">
    <svg width="185" height="84" viewBox="0 0 185 84" style="position:absolute;inset:0">
      <path d="M0 0 H185 V28 L92.5 58 L0 28Z" fill="var(--brand-blue)"/>
      <path d="M0 84 L92.5 50 L185 84" fill="none" stroke="#d8dce4" stroke-width="1"/>
    </svg>
  </div>

  <div class="sheet envelope env-plain">
    <svg width="185" height="80" viewBox="0 0 185 80" style="position:absolute;inset:0">
      <path d="M0 0 L92.5 36 L185 0" fill="none" stroke="#d8dce4" stroke-width="1"/>
      <path d="M0 80 L80 44 M185 80 L105 44" fill="none" stroke="#e3e6ec" stroke-width="1"/>
    </svg>
  </div>

  <div class="sheet envelope env-long">
    <div class="wordmark"><span class="mark-box"></span>The Montrevo Group</div>
    <p class="tagline">Franchise Consulting Services</p>
    <svg class="wave" viewBox="0 0 360 70" preserveAspectRatio="none" height="34">
      <path d="M0 32 C110 4 230 54 360 16 L360 70 L0 70Z" fill="var(--brand-blue)"/>
      <path d="M0 24 C110 -4 230 48 360 8" fill="none" stroke="var(--brand-blue-light)" stroke-width="1.4"/>
    </svg>
  </div>
  <p class="caption" style="left:1008px; top:423px; width:185px;">Envelope Options</p>

</body>
</html>
```